Computer consultant business card

Bexil Software is a newly started computer consulting company. It's a small one-man company that provides mostly Vornix applications but also websites in collaboration with designers. I'm running this company on the side of full time university studies.

I want the final design to be clean and memorable. Be creative! :)

Some inspiration:
http://www.pixelmarta.com/design/48317
http://www.pixelmarta.com/design/2739164/business-card-design-by-frostlynk
http://www.pixelmarta.com/design/604281/business-card-design-by-koralind-vestrabanu

See attachment for my company logo.
Updates

I would like to thank everyone for submitting! I'll need a couple of days to review and ultimately select a design.

Target Market(s)

Non-technical entrepreneurs and small companies.

Industry/Entity Type

University

Requirements
Must have
• My company logo.
In any way, both colors from my logo.
First- and last name, e-mail and phone number.
Double-sided design.
Nice to have
• Something creative with the symbol in my logo

```html
<!DOCTYPE html>
<html lang="en">
<head>
<meta charset="utf-8">
<title>Bexil Software – Business Card</title>
<link rel="stylesheet" href="https://fonts.googleapis.com/css2?family=Arimo:wght@400;700&display=swap">
<style>
  :root {
    --brand-blue: #2479f0;
    --brand-dark: #333336;
    --card-white: #ffffff;
    --backdrop: #e9eaec;
    --pattern-light: #3a88f3;
  }
  * { margin: 0; padding: 0; box-sizing: border-box; }
  html, body { width: 1200px; height: 820px; overflow: hidden; }
  body {
    background: var(--backdrop);
    font-family: "Arimo", Arial, sans-serif;
    position: relative;
  }
  .card {
    position: absolute;
    width: 540px;
    height: 310px;
    box-shadow: 0 6px 18px rgba(0,0,0,0.18);
    overflow: hidden;
  }

  /* Front side */
  .card-front {
    left: 50px;
    top: 110px;
    background: var(--card-white);
  }
  .name-band {
    height: 40px;
    background: var(--brand-blue);
    color: var(--card-white);
    display: flex;
    align-items: center;
    justify-content: center;
    font-size: 19px;
    gap: 6px;
  }
  .name-band .first-name { font-weight: 700; }
  .rule {
    position: absolute;
    left: 0; right: 0;
    height: 3px;
    background: var(--brand-dark);
  }
  .rule-top { top: 44px; }
  .rule-bottom { bottom: 44px; }
  .front-logo {
    position: absolute;
    top: 90px;
    left: 0; right: 0;
    display: flex;
    align-items: center;
    justify-content: center;
    gap: 20px;
  }
  .logo-dot {
    width: 84px; height: 84px;
    border-radius: 50%;
    background: var(--brand-blue);
  }
  .logo-name {
    font-size: 92px;
    font-weight: 700;
    color: var(--brand-dark);
    letter-spacing: -1px;
    line-height: 1;
  }
  .contact-line {
    position: absolute;
    bottom: 56px;
    left: 0; right: 0;
    display: flex;
    justify-content: center;
    gap: 22px;
    font-size: 14px;
    color: var(--brand-dark);
  }
  .contact-item { display: flex; align-items: center; gap: 6px; }
  .contact-item svg { width: 13px; height: 13px; fill: var(--brand-dark); }
  .address-band {
    position: absolute;
    bottom: 0; left: 0; right: 0;
    height: 40px;
    background: var(--brand-blue);
    color: var(--card-white);
    display: flex;
    align-items: center;
    justify-content: center;
    font-size: 14px;
    letter-spacing: 0.5px;
  }

  /* Back side */
  .card-back {
    left: 610px;
    top: 400px;
    background: var(--brand-blue);
  }
  .back-pattern {
    position: absolute;
    inset: 0;
    background: linear-gradient(135deg, var(--pattern-light), var(--brand-blue) 60%);
  }
  .back-logo {
    position: absolute;
    inset: 0;
    display: flex;
    align-items: center;
    justify-content: center;
    font-size: 110px;
    font-weight: 700;
    color: var(--card-white);
    letter-spacing: -1px;
  }
</style>
</head>
<body>

  <section class="card card-front" aria-label="Business card front">
    <header class="name-band">
      <span class="first-name">First Name,</span>
      <span class="last-name">Last Name</span>
    </header>
    <div class="rule rule-top"></div>

    <div class="front-logo">
      <span class="logo-dot"></span>
      <span class="logo-name">bexil</span>
    </div>

    <div class="contact-line">
      <span class="contact-item">
        <svg viewBox="0 0 24 24" aria-hidden="true"><path d="M6.6 10.8a15.1 15.1 0 0 0 6.6 6.6l2.2-2.2c.3-.3.7-.4 1-.2 1.1.4 2.3.6 3.6.6.6 0 1 .4 1 1V20c0 .6-.4 1-1 1A17 17 0 0 1 3 4c0-.6.4-1 1-1h3.5c.6 0 1 .4 1 1 0 1.3.2 2.5.6 3.6.1.3 0 .7-.2 1z"/></svg>
        0987 654321
      </span>
      <span class="contact-item">
        <svg viewBox="0 0 24 24" aria-hidden="true"><path d="M2 6h20v12H2z M2 6l10 7 10-7" fill="none" stroke="#333336" stroke-width="2.4"/></svg>
        info@bexil.com
      </span>
    </div>

    <div class="rule rule-bottom"></div>
    <footer class="address-band">00, Complex name, City, State 0042</footer>
  </section>

  <section class="card card-back" aria-label="Business card back">
    <div class="back-pattern" role="img" aria-label="Faint repeating brand pattern across the blue background"></div>
    <div class="back-logo">bexil</div>
  </section>

</body>
</html>
```